Children’s entertainer/balloon artist Website Home Page and custom landing page

I need a home page design for the home page of a children and family entertainer/balloon twister’s website. I also need a custom landing page for family theatre shows performed by the same entertainer.
It will be a Wordpress website and I need the final artwork in a layer Photoshop file with all the layers clearly named and labeled.

Target Market(s)

The site visitors are mainly mums, aged between early 20’s and late 30’s. Other visitors will included companies for Christmas functions, and event organisers for corporate functions.

Industry/Entity Type

Entertainment

Number of Pages Required

2 page

Font styles to use
Sans Serif

Colors
34a6d7
f37122

Requirements
Must have
• Layout
• I have included a wireframe for the home page layout and the custom landing page for your reference. This is a guide only and I welcome your interpretation with the rough layout provided.
• This website needs to look good on all devices as it will be fully responsive.
• It needs to include a footer area on the page, that has social media and a call to action area included.
• Colours
• The main colours for the site is:
• orange (call to action colour)
• ff6800
• blue/turquoise
• 42abc3
• Pictures
• I have included images of the entertainer/balloon artist for you to use/take inspiration from.
• These images will be included on the website. I want to show lots of people having fun.
• I would like to have elements of the logo used in isolation across the website
• i.e. the octopus figure to be included in the footer or the bird element to be included in the testimonial slider etc.
• Elements to include
• Note: use the images of the entertainer in the boxes on the home page (balloon shows, balloon twisting, balloon workshops, theatre shows (the three little balloon pigs on his head)
Nice to have
Should not have
• Element to avoid
• Stock imagery of balloon sculptures - use images provided.

```html
<!DOCTYPE html>
<html lang="en">
<head>
<meta charset="utf-8">
<title>Benny Marlowe – Kids Entertainer and Balloon Artist</title>
<link href="https://fonts.googleapis.com/css2?family=Lato:wght@400;700;900&display=swap" rel="stylesheet">
<style>
:root{
  --blue:#34a6d7;
  --blue-deep:#1d3f8f;
  --blue-mid:#2a5fb8;
  --orange:#f37122;
  --ink:#333;
  --muted:#888;
  --line:#e2e2e2;
  --band:#eef1f4;
  --white:#fff;
}
*{box-sizing:border-box;margin:0;padding:0}
html,body{width:694px;height:1200px;overflow:hidden}
body{font-family:'Lato',sans-serif;color:var(--ink);background:var(--white);position:relative}

/* header */
.site-header{position:absolute;left:0;top:0;width:694px;height:51px;background:var(--white);z-index:3}
.brand{position:absolute;left:12px;top:6px;width:96px;height:84px;border-radius:10px;background:var(--white);display:flex;flex-direction:column;align-items:center;justify-content:center;gap:5px;z-index:4}
.brand-dot{width:36px;height:36px;border-radius:50%;background:var(--orange)}
.brand-name{font-weight:900;font-size:11px;color:var(--blue-deep);text-align:center;line-height:1.1}
.header-balloon{position:absolute;left:196px;top:6px;width:28px;height:38px;border-radius:50% 50% 48% 48%;background:var(--blue)}
.header-string{position:absolute;left:209px;top:44px;width:1px;height:14px;background:#999}
.main-nav{position:absolute;left:240px;top:25px;display:flex;gap:18px;font-size:9px;color:var(--ink)}
.phone{position:absolute;left:590px;top:25px;font-size:9px;font-weight:700;color:var(--orange);display:flex;align-items:center;gap:4px}

/* hero */
.hero{position:absolute;left:0;top:51px;width:694px;height:411px;background:linear-gradient(90deg,var(--blue-deep) 0%,var(--blue-mid) 55%,#4f86d6 80%,var(--blue-mid) 100%);overflow:hidden}
.hero-photo{position:absolute;left:300px;top:10px;width:380px;height:401px;background:radial-gradient(ellipse at 60% 60%,#6fa3e6 0%,#3d73c9 45%,rgba(42,95,184,0) 75%)}
.hero-label{position:absolute;left:58px;top:132px;font-size:11px;font-weight:700;letter-spacing:.5px;color:var(--white)}
.hero-name{position:absolute;left:58px;top:146px;font-size:32px;font-weight:900;line-height:40px;color:var(--white);letter-spacing:.5px}
.hero-rule{position:absolute;left:58px;top:188px;width:60px;height:3px;background:var(--orange)}
.ticks{position:absolute;left:58px;top:200px;list-style:none}
.ticks li{display:flex;align-items:center;gap:10px;height:29px;font-size:14px;font-weight:700;color:var(--white)}
.btn{display:inline-flex;align-items:center;justify-content:center;background:var(--orange);color:var(--white);font-weight:700;font-size:9px;letter-spacing:.5px;text-transform:uppercase}
.hero .btn{position:absolute;left:58px;top:334px;width:92px;height:24px}
.dots{position:absolute;left:333px;top:385px;display:flex;gap:5px}
.dots span{width:6px;height:6px;border-radius:50%;background:#9ab8e6}
.dots span:first-child{background:var(--white)}

/* content */
.section-title{font-size:17px;font-weight:700;color:var(--ink)}
.title-rule{width:28px;height:2px;background:var(--orange);margin-top:6px}
.testimonials{position:absolute;left:58px;top:493px}
.slider-arrows{position:absolute;left:397px;top:493px;display:flex;gap:3px}
.slider-arrows span{width:13px;height:13px;background:#bbb}
.slider-arrows span:last-child{background:var(--blue)}
.quote{position:absolute;top:531px;width:175px;height:66px;border:1px solid var(--line);padding:9px 10px;font-size:7px;line-height:1.6;color:var(--muted);overflow:hidden}
.quote-author{position:absolute;top:604px;display:flex;align-items:center;gap:8px;font-size:7px;color:var(--muted)}
.avatar{width:20px;height:20px;border-radius:50%;background:#b9a58f}
.panel{position:absolute;left:450px;width:208px;background:var(--white);box-shadow:0 1px 6px rgba(0,0,0,.15);padding:14px 16px}
.panel .section-title{font-size:15px}
.panel p{font-size:7px;line-height:1.6;color:var(--muted);margin:10px 0}
.panel .btn{width:80px;height:18px;font-size:7px;margin:0 auto;display:flex}
.callback{top:485px;height:127px}
.contact{top:647px;height:173px}
.field{height:20px;border:1px solid var(--line);font-size:7px;color:var(--muted);padding:6px 6px;margin-top:6px}
.field.tall{height:36px}
.contact .btn{margin-top:10px}

.welcome{position:absolute;left:58px;top:650px}
.welcome-art{position:absolute;left:58px;top:690px;width:116px;height:112px;background:radial-gradient(circle at 50% 45%,#f4a04c 0%,#5aa9d8 45%,#ffffff 78%)}
.welcome-text{position:absolute;left:192px;top:664px;width:226px;font-size:7px;line-height:1.6;color:var(--muted)}
.read-more{position:absolute;left:192px;top:790px;font-size:7px;font-weight:700;color:var(--ink)}

/* services */
.services{position:absolute;left:0;top:852px;width:694px;height:291px;background:var(--band)}
.service{position:absolute;top:40px;width:127px;text-align:center}
.service-photo{width:127px;height:132px}
.service h3{font-size:11px;font-weight:400;color:var(--ink);margin:10px 0 6px}
.service .btn{width:42px;height:14px;font-size:6px;background:#9a9a9a}
.service:first-child .btn{background:var(--orange)}

/* footer */
.site-footer{position:absolute;left:0;top:1143px;width:694px;height:57px;background:var(--blue)}
.footer-cta{position:absolute;left:230px;top:11px;display:flex;align-items:center;gap:14px;font-size:9px;color:var(--white)}
.footer-cta .btn{width:96px;height:18px;font-size:8px;text-transform:none;font-weight:400}
.footer-links{position:absolute;left:230px;top:37px;display:flex;gap:14px;font-size:6px;color:var(--white)}
.copyright{position:absolute;left:230px;top:47px;font-size:5px;color:#d8eefb}
.social{position:absolute;left:590px;top:36px;display:flex;gap:5px}
.social span{width:12px;height:12px;border-radius:50%;border:1px solid var(--white)}
.footer-art{position:absolute;left:0;top:1105px;width:90px;height:95px;border-radius:0 55px 0 0;background:radial-gradient(circle at 40% 50%,#7bbf4a 0%,#3b8f3a 55%,rgba(52,166,215,0) 80%);z-index:2}
</style>
</head>
<body>

<header class="site-header">
  <div class="brand"><span class="brand-dot"></span><span class="brand-name">Benny's Balloons</span></div>
  <span class="header-balloon"></span><span class="header-string"></span>
  <nav class="main-nav"><span>Balloon Shows</span><span>Balloon Twisting</span><span>Theatre</span><span>Reviews</span><span>Contact</span></nav>
  <div class="phone">
    <svg width="9" height="9" viewBox="0 0 24 24"><path fill="#f37122" d="M6.6 10.8a15 15 0 0 0 6.6 6.6l2.2-2.2c.3-.3.7-.4 1-.2 1.1.4 2.3.6 3.6.6.6 0 1 .4 1 1V20c0 .6-.4 1-1 1A17 17 0 0 1 3 4c0-.6.4-1 1-1h3.5c.6 0 1 .4 1 1 0 1.3.2 2.5.6 3.6.1.3 0 .7-.2 1z"/></svg>
    +44 000 123 456
  </div>
</header>

<section class="hero">
  <div class="hero-photo" role="img" aria-label="Photo of the entertainer in a blue suit holding a speaker on a stick under a spotlight"></div>
  <div class="hero-label">KIDS ENTERTAINER AND BALLOON ARTIST</div>
  <h1 class="hero-name">BENNY MARLOWE</h1>
  <div class="hero-rule"></div>
  <ul class="ticks">
    <li><svg width="16" height="16" viewBox="0 0 16 16"><circle cx="8" cy="8" r="8" fill="#fff"/><path d="M4.5 8.2l2.3 2.3 4.7-4.8" stroke="#1d3f8f" stroke-width="1.8" fill="none"/></svg>Nunc aliquam leo nec</li>
    <li><svg width="16" height="16" viewBox="0 0 16 16"><circle cx="8" cy="8" r="8" fill="#fff"/><path d="M4.5 8.2l2.3 2.3 4.7-4.8" stroke="#1d3f8f" stroke-width="1.8" fill="none"/></svg>Diam pellentesque</li>
    <li><svg width="16" height="16" viewBox="0 0 16 16"><circle cx="8" cy="8" r="8" fill="#fff"/><path d="M4.5 8.2l2.3 2.3 4.7-4.8" stroke="#1d3f8f" stroke-width="1.8" fill="none"/></svg>Hendrerit. Vestibulum eu</li>
    <li><svg width="16" height="16" viewBox="0 0 16 16"><circle cx="8" cy="8" r="8" fill="#fff"/><path d="M4.5 8.2l2.3 2.3 4.7-4.8" stroke="#1d3f8f" stroke-width="1.8" fill="none"/></svg>Neque eget ex</li>
  </ul>
  <span class="btn">Call Now</span>
  <div class="dots"><span></span><span></span><span></span></div>
</section>

<div class="testimonials"><h2 class="section-title">Testimonials</h2><div class="title-rule"></div></div>
<div class="slider-arrows"><span></span><span></span></div>
<blockquote class="quote" style="left:58px">Lorem ipsum dolor sit amet, consectetur adipiscing elit. Integer nec odio praesent libero, sed cursus ante dapibus diam. Sed nisi nulla quis sem at nibh elementum.</blockquote>
<blockquote class="quote" style="left:243px">Curabitur sodales ligula in libero. Sed dignissim lacinia nunc, curabitur tortor pellentesque nibh aenean quam. In scelerisque sem at dolor maecenas mattis.</blockquote>
<div class="quote-author" style="left:80px"><span class="avatar"></span>Sarah Lane</div>
<div class="quote-author" style="left:265px"><span class="avatar"></span>Mark Hill</div>

<aside class="panel callback">
  <h2 class="section-title">Request a call back</h2>
  <p>Lorem ipsum dolor sit amet, consectetur adipiscing elit. Ut luctus placerat libero, non posuere nisi.</p>
  <span class="btn">Request Now</span>
</aside>

<div class="welcome"><h2 class="section-title">Welcome</h2><div class="title-rule"></div></div>
<div class="welcome-art" role="img" aria-label="Illustration of a balloon figure holding a sign"></div>
<p class="welcome-text">Nullam quis risus eget urna mollis ornare vel eu leo. Cum sociis natoque penatibus et magnis dis parturient montes, nascetur ridiculus mus. Donec ullamcorper nulla non metus auctor fringilla. Vestibulum id ligula porta felis euismod semper. Maecenas faucibus mollis interdum. Aenean lacinia bibendum nulla sed consectetur. Cras mattis consectetur purus sit amet fermentum.</p>
<span class="read-more">Read More »</span>

<aside class="panel contact">
  <h2 class="section-title">Contact Now</h2>
  <div class="field">Name</div>
  <div class="field">Email</div>
  <div class="field tall">Message</div>
  <span class="btn">Contact Now</span>
</aside>

<section class="services">
  <div class="service" style="left:65px"><div class="service-photo" role="img" aria-label="Photo of the entertainer surrounded by colourful balloon shapes" style="background:linear-gradient(160deg,#3d5fb0,#e3a23c 60%,#c8462f)"></div><h3>Balloon shows</h3><span class="btn">More</span></div>
  <div class="service" style="left:208px"><div class="service-photo" role="img" aria-label="Photo of the entertainer twisting balloons" style="background:linear-gradient(160deg,#f0b43a,#6db4d9 55%,#3b7fc0)"></div><h3>Balloon Twisting</h3><span class="btn">More</span></div>
  <div class="service" style="left:347px"><div class="service-photo" role="img" aria-label="Photo of children at a balloon workshop" style="background:linear-gradient(160deg,#a07a5a,#d9b28c 50%,#5a4a3e)"></div><h3>Balloon Workshop</h3><span class="btn">More</span></div>
  <div class="service" style="left:490px"><div class="service-photo" role="img" aria-label="Photo of the entertainer with three pink balloon pigs on his head" style="background:linear-gradient(160deg,#e7e1dc,#f08cb0 50%,#d96a94)"></div><h3>Theatre Shows</h3><span class="btn">More</span></div>
</section>

<div class="footer-art" role="img" aria-label="Decorative balloon character"></div>
<footer class="site-footer">
  <div class="footer-cta">Lorem ipsum dolor sit amet, consectetur<span class="btn">Request a call back</span></div>
  <nav class="footer-links"><span>Home</span><span>Balloon Shows</span><span>Balloon Twisting</span><span>Theatre</span><span>Reviews</span><span>Contact</span></nav>
  <div class="copyright">© 2024 Benny's Balloons. All Rights Reserved.</div>
  <div class="social"><span></span><span></span><span></span><span></span></div>
</footer>

</body>
</html>
```